Beautiful design for wordpress

I need a beautiful, colourful and feminine website. My business is called 'The Velvet Lantern', and I sell crystals, books, CD's, pendulums and other metaphysical items. I also provide Reiki (energy healing).
I want this design to be eye catching and inspire happiness and joy in those who see it. And I would love to see the use of the logo and its colours :)
Please add these on the web design: Home, About, Online store, Blog

Industry/Entity Type

Business

Requirements
Must have
• Colourful and playful, must use the logo somewhere, have the words on a menu saying 'Home, Blog, Online store and about' (or similar to those)And the design must stand out!
Should not have
• grey, brown and other boring colours.

```html
<!DOCTYPE html>
<html lang="en">
<head>
<meta charset="utf-8">
<title>The Velvet Lantern – Crystals &amp; Gifts</title>
<link rel="stylesheet" href="https://fonts.googleapis.com/css2?family=Open+Sans:ital,wght@0,400;0,600;0,700;1,400&display=swap">
<style>
  :root{
    --pink:#e6108c;
    --pink-soft:#f27ac4;
    --orange:#f39200;
    --ink:#222;
    --text:#444;
    --muted:#666;
    --rule:#cfcfcf;
    --footer:#3a3a3a;
    --footer-deep:#2a2a2a;
    --white:#fff;
  }
  *{box-sizing:border-box;margin:0;padding:0}
  html,body{width:842px;height:1200px;overflow:hidden;background:var(--white)}
  body{position:relative;font-family:"Open Sans",Arial,sans-serif;color:var(--ink)}
  .abs{position:absolute}

  /* header */
  .brand{left:62px;top:30px;width:150px}
  .brand-name{display:flex;align-items:center;gap:6px;font-size:17px;font-weight:600;color:var(--pink);line-height:1.1}
  .brand-dot{width:12px;height:12px;border-radius:50%;background:var(--orange);flex:none}
  .brand-tag{margin-top:6px;padding-left:18px;font-size:7px;letter-spacing:1.6px;color:var(--muted);font-weight:600}
  .search{left:535px;top:17px;width:229px;height:24px;border:1px solid #ccc;display:flex}
  .search span{flex:1;font-size:9px;color:#555;padding:5px 13px}
  .search b{width:33px;background:#111;display:flex;align-items:center;justify-content:center}
  .phone{left:538px;top:56px;display:flex;align-items:center;gap:8px;font-size:13px;color:#333}
  .cart{left:678px;top:59px;font-size:10px;color:#222;display:flex;align-items:center;gap:5px}
  .cart-count{left:729px;top:77px;font-size:8px;color:#222}
  .rule-top{left:62px;top:91px;width:704px;height:1px;background:#ddd}
  .rule-nav{left:62px;top:130px;width:704px;height:1px;background:#ddd}
  .nav{top:105px;font-size:10px;color:#111}
  .nav.active{color:var(--orange)}
  .nav-caret{left:403px;top:126px;width:0;height:0;border-left:3px solid transparent;border-right:3px solid transparent;border-bottom:3px solid var(--orange)}

  /* hero */
  .hero{left:69px;top:151px;width:696px;height:245px;border:1px solid #ddd;
    background:radial-gradient(ellipse at 72% 45%,#e9e4da 0%,#b9b3a6 22%,#4a4844 42%,#050505 62%)}
  .hero-panel{left:62px;top:254px;width:319px;height:126px;background:rgba(236,105,190,.92);text-align:right;padding:20px 17px 0 10px;color:var(--white)}
  .hero-panel h2{font-size:17px;font-weight:400;margin-bottom:6px}
  .hero-panel p{font-size:10px;line-height:21px}
  .hero-panel a{display:block;margin-top:1px;font-size:9px;font-weight:600;color:#111;text-decoration:none}
  .slider-nav{left:302px;top:410px;display:flex;align-items:center;font-size:9px;color:#333}
  .dots{display:flex;gap:6px;margin:0 22px 0 22px}
  .dots i{width:9px;height:9px;border-radius:50%;background:#333}
  .dots i.on{background:var(--pink)}
  .rule-dot{left:71px;top:450px;width:694px;border-top:1px dotted #bbb}

  /* welcome */
  .welcome-img{left:70px;top:475px;width:262px;height:140px;
    background:radial-gradient(circle at 50% 50%,#ffffff 0%,#b9c8de 12%,#d27ac6 28%,#5b1a4d 55%,#0a0a0a 80%)}
  .welcome h1{left:354px;top:472px;font-size:15px;font-weight:400;color:#333}
  .welcome h1 em{font-style:normal;color:var(--pink)}
  .welcome p{left:357px;top:503px;width:400px;font-size:8.8px;line-height:12.6px;color:#333}
  .more{left:358px;top:601px;font-size:8.5px;color:var(--pink);font-weight:600}

  /* products */
  .section-title{left:74px;top:662px;font-size:15px;color:#333}
  .section-title em{font-style:normal;color:var(--pink)}
  .rule-products{left:71px;top:689px;width:694px;border-top:1px dotted #bbb}
  .tabbox{left:69px;top:757px;width:696px;height:248px;border:1px solid #ccc}
  .tab-active{left:69px;top:725px;width:110px;height:33px;border:1px solid #ccc;border-bottom:1px solid var(--white);background:var(--white);
    font-size:11px;font-weight:600;color:var(--pink);text-align:center;line-height:31px}
  .tabs{left:200px;top:733px;display:flex;gap:16px;font-size:11.5px;color:#222}
  .arrow{top:768px;width:14px;height:15px;background:var(--orange);display:flex;align-items:center;justify-content:center}
  .product{top:797px;width:138px}
  .product-img{width:138px;height:78px}
  .product h3{margin-top:12px;font-size:11.5px;font-weight:400;color:#333}
  .product p{margin-top:4px;font-size:8.8px;line-height:12.5px;color:#666}
  .buy-row{margin-top:7px;display:flex;justify-content:space-between;align-items:center}
  .price{font-size:12.5px;color:var(--pink);padding-left:4px}
  .buy{width:75px;height:25px;background:#111;border-radius:2px;color:var(--pink);font-size:9.5px;text-align:center;line-height:25px}

  /* footer */
  .footer{left:0;top:1039px;width:842px;height:125px;background:var(--footer)}
  .footer-bar{left:0;top:1164px;width:842px;height:36px;background:var(--footer-deep);color:#ddd;font-size:8px;text-align:center;line-height:36px}
  .f-title{top:1058px;font-size:12px;color:var(--white)}
  .f-line{left:78px;display:flex;align-items:center;gap:9px;color:#eee;font-size:9px;line-height:13px}
  .f-line svg{flex:none}
  .email-field{left:333px;top:1084px;width:159px;height:22px;background:var(--white);border:1px solid #bbb;font-size:7.5px;font-style:italic;color:#888;padding:5px 11px}
  .subscribe{left:418px;top:1120px;width:73px;height:22px;background:#ff2d9b;border-radius:2px;color:var(--white);font-size:10px;font-weight:600;text-align:center;line-height:22px}
  .socials{left:636px;top:1090px;display:flex;gap:12px}
  .socials i{width:16px;height:16px;border-radius:2px}
  .pays{left:643px;top:1121px;display:flex;gap:6px}
  .pays i{width:20px;height:13px;border-radius:1px;background:#e8e8e8}
</style>
</head>
<body>

<header>
  <div class="abs brand">
    <div class="brand-name"><span class="brand-dot"></span>The Velvet Lantern</div>
    <div class="brand-tag">CRYSTALS &amp; GIFTS</div>
  </div>

  <div class="abs search">
    <span>Search</span>
    <b><svg width="10" height="10" viewBox="0 0 10 10"><circle cx="4" cy="4" r="3" fill="none" stroke="#e6108c" stroke-width="1.6"/><line x1="6.2" y1="6.2" x2="9" y2="9" stroke="#e6108c" stroke-width="1.8"/></svg></b>
  </div>

  <div class="abs phone">
    <svg width="19" height="14" viewBox="0 0 19 14"><path d="M2 2 Q9 -1 17 2 L15.5 5.5 L12.5 4.5 L12 3 Q9.5 2.2 7 3 L6.5 4.5 L3.5 5.5 Z" fill="#333" transform="rotate(20 9 5)"/><rect x="5" y="8" width="9" height="5" rx="1" fill="#333"/></svg>
    1-888-555-0142
  </div>
  <div class="abs cart">
    <svg width="15" height="12" viewBox="0 0 15 12"><path d="M1 1 H3 L5 8 H12 L14 3 H4" fill="none" stroke="#333" stroke-width="1.1"/><circle cx="6" cy="10.5" r="1" fill="#333"/><circle cx="11" cy="10.5" r="1" fill="#333"/></svg>
    Shopping Cart
  </div>
  <div class="abs cart-count">0 Items</div>

  <div class="abs rule-top"></div>
  <nav>
    <span class="abs nav active" style="left:392px">HOME</span>
    <span class="abs nav" style="left:458px">ABOUT US</span>
    <span class="abs nav" style="left:540px">ONLINE STORE</span>
    <span class="abs nav" style="left:646px">BLOG</span>
    <span class="abs nav" style="left:706px">CONTACT US</span>
  </nav>
  <div class="abs nav-caret"></div>
  <div class="abs rule-nav"></div>
</header>

<section>
  <div class="abs hero" role="img" aria-label="Cluster of clear quartz crystals on a black background"></div>
  <div class="abs hero-panel">
    <h2>Nunc Et Augue A Sapien</h2>
    <p>Vivamus non erat et est sodales pretium eu quis orci.<br>Nunc et augue a sapien pharetra molestie.</p>
    <a>Read More &gt;&gt;</a>
  </div>
  <div class="abs slider-nav">
    <span>&#8249;&nbsp; Previous</span>
    <span class="dots"><i></i><i></i><i></i><i></i><i class="on"></i></span>
    <span>Next &nbsp;&#8250;</span>
  </div>
  <div class="abs rule-dot"></div>
</section>

<section class="welcome">
  <div class="abs welcome-img" role="img" aria-label="Hands cupped around a glowing globe of the earth with pink light"></div>
  <h1 class="abs">Welcome to <em>The Velvet Lantern</em></h1>
  <p class="abs">Lorem ipsum dolor sit amet, consectetur adipiscing elit. Aliquam et lacus quam. Proin facilisis ante quis justo fringilla pretium. Duis condimentum dui eget nunc consectetur consectetur. Aenean aliquet mi ut nisi malesuada volutpat. Sed turpis justo, convallis ut porta ac, tempor at lorem. Nunc porta nisl enim, et posuere erat malesuada ut. Morbi porta nec dui id dignissim. Donec dapibus velit in enim euismod, quis vulputate mi elementum. Sed rhoncus ipsum non dolor luctus fringilla. Vivamus feugiat turpis enim, at laoreet dolor aliquet quis. Nunc at justo placerat, pulvinar libero at, dignissim elit.</p>
  <span class="abs more">More &gt;&gt;</span>
</section>

<section>
  <h2 class="abs section-title" style="font-weight:400">Our <em>Products</em></h2>
  <div class="abs rule-products"></div>

  <div class="abs tabbox"></div>
  <div class="abs tab-active">Crystals</div>
  <div class="abs tabs"><span>Books</span><span>|</span><span>CD's</span><span>|</span><span>Pendulums</span><span>|</span><span>Other Metaphysical items</span></div>

  <div class="abs arrow" style="left:704px"><svg width="6" height="8" viewBox="0 0 6 8"><path d="M5 1 L2 4 L5 7" fill="none" stroke="#fff" stroke-width="1.6"/></svg></div>
  <div class="abs arrow" style="left:725px"><svg width="6" height="8" viewBox="0 0 6 8"><path d="M1 1 L4 4 L1 7" fill="none" stroke="#fff" stroke-width="1.6"/></svg></div>

  <div class="abs product" style="left:94px">
    <div class="product-img" role="img" aria-label="Blue fluorite crystal with white quartz" style="background:linear-gradient(135deg,#1b5f7a,#44b3d6 45%,#d8e6ea 70%,#2a3b42)"></div>
    <h3>Aenean Elementum</h3>
    <p>Curabitur congue lorem massa, quis ultrices nibh rhoncus vel. Nunc quis sapien et nisl ultrices</p>
    <div class="buy-row"><span class="price">$25.95</span><span class="buy">Buy Now</span></div>
  </div>
  <div class="abs product" style="left:264px">
    <div class="product-img" role="img" aria-label="Purple amethyst crystal points" style="background:linear-gradient(110deg,#5a1e6e,#b06ad0 40%,#e4c5f0 55%,#7a3a99)"></div>
    <h3>Aenean Elementum</h3>
    <p>Curabitur congue lorem massa, quis ultrices nibh rhoncus vel. Nunc quis sapien et nisl ultrices</p>
    <div class="buy-row"><span class="price">$25.95</span><span class="buy">Buy Now</span></div>
  </div>
  <div class="abs product" style="left:433px">
    <div class="product-img" role="img" aria-label="Clear blue crystal cluster" style="background:radial-gradient(ellipse at 50% 60%,#c5dbf2,#6f93c4 45%,#1d2f52)"></div>
    <h3>Aenean Elementum</h3>
    <p>Curabitur congue lorem massa, quis ultrices nibh rhoncus vel. Nunc quis sapien et nisl ultrices</p>
    <div class="buy-row"><span class="price">$25.95</span><span class="buy">Buy Now</span></div>
  </div>
  <div class="abs product" style="left:602px">
    <div class="product-img" role="img" aria-label="Crystal pendulums hanging on red cords over purple cloth" style="background:linear-gradient(160deg,#4b1a8a,#8c3fd0 55%,#5c22a0)"></div>
    <h3>Aenean Elementum</h3>
    <p>Curabitur congue lorem massa, quis ultrices nibh rhoncus vel. Nunc quis sapien et nisl ultrices</p>
    <div class="buy-row"><span class="price">$25.95</span><span class="buy">Buy Now</span></div>
  </div>
</section>

<footer>
  <div class="abs footer"></div>
  <h4 class="abs f-title" style="left:69px;top:1059px;font-weight:400">CONTACT INFO</h4>
  <h4 class="abs f-title" style="left:333px;font-weight:400">NEWSLETTER</h4>
  <h4 class="abs f-title" style="left:653px;font-weight:400">CONNECT WITH US</h4>

  <div class="abs f-line" style="top:1086px">
    <svg width="14" height="13" viewBox="0 0 14 13"><path d="M7 1 L13 6.5 H11 V12 H3 V6.5 H1 Z" fill="#aaa"/></svg>
    <span>Loreum Ipsum Dollar,<br>Sit Amet</span>
  </div>
  <div class="abs f-line" style="top:1117px;font-size:12.5px">
    <svg width="14" height="12" viewBox="0 0 14 12"><path d="M1 3 Q7 -1 13 3 L12 5 L9 4.5 V3.5 H5 V4.5 L2 5 Z" fill="#aaa"/><rect x="3" y="6" width="8" height="5" rx="1" fill="#aaa"/></svg>
    <span>1-888-555-0142</span>
  </div>
  <div class="abs f-line" style="top:1141px">
    <svg width="14" height="10" viewBox="0 0 14 10"><rect x="0.5" y="0.5" width="13" height="9" fill="none" stroke="#aaa"/><path d="M0.5 0.5 L7 6 L13.5 0.5" fill="none" stroke="#aaa"/></svg>
    <span>hello@velvetlantern-shop.com</span>
  </div>

  <div class="abs email-field">Your Email Id</div>
  <div class="abs subscribe">Subscribe</div>

  <div class="abs socials">
    <i style="background:#3b5aa0"></i>
    <i style="background:#4fb0e0"></i>
    <i style="background:#f07a22"></i>
    <i style="background:#1a76b0"></i>
    <i style="background:#4caf50"></i>
  </div>
  <div class="abs pays"><i></i><i></i><i></i><i></i><i></i></div>

  <div class="abs footer-bar">© 2014 The Velvet Lantern. All rights reserved</div>
</footer>

</body>
</html>
```